business card for horse saddlery

after a new business card for our saddlery, i will add 2 logos we have previously used and they can be used (or not) . Any images can be used from our website also at www.harrowfields.net.au, I have also added our brand logo, which may be good to incorporate on back ? we have over 15, 000 items online, ship Australia Wide.

Target Market(s)

horse owners

Industry/Entity Type

Retail - Equestrian

Contact Information for Business Card

Harrowfield Horse Supplies, 1300 48 62 90, www.harrowfields.net.au, 27 Lindqvist Rd Marrowbank Q 4587

Requirements
Must have
• trailgem is our brand so trailgem logo on back as 'distributers of', easy to read
Nice to have
• professional but fun
Should not have
• double sided (description wont save double sided)

```html
<!DOCTYPE html>
<html lang="en">
<head>
<meta charset="utf-8">
<title>Harrowfield Horse Supplies – Business Card</title>
<link href="https://fonts.googleapis.com/css2?family=Open+Sans:wght@400;600;700&display=swap" rel="stylesheet">
<style>
  :root {
    --bg: #2b2e33;
    --card-white: #f5f5f5;
    --navy: #26357a;
    --amber: #f5a412;
    --gold: #fbb41c;
    --gold-deep: #c98a0c;
    --ink: #1c1c1c;
    --leaf: #4f8a3a;
    --leaf-dark: #2f5e25;
    --leaf-light: #8fbf5d;
  }
  * { box-sizing: border-box; margin: 0; padding: 0; }
  html, body {
    width: 1200px; height: 780px; overflow: hidden;
    background: var(--bg);
    font-family: "Open Sans", Arial, sans-serif;
  }
  .canvas { position: relative; width: 1200px; height: 780px; }
  .card {
    position: absolute; top: 230px;
    width: 560px; height: 320px;
    border-radius: 4px; overflow: hidden;
    box-shadow: 0 14px 30px rgba(0,0,0,.45);
  }
  .card--front { left: 30px; background: var(--card-white); }
  .card--back { left: 610px; background: var(--gold); }

  .card__art { position: absolute; inset: 0; }

  .brand {
    position: absolute; left: 28px; top: 26px;
    display: flex; align-items: center; gap: 8px;
    color: var(--navy); font-weight: 700; font-size: 15px; line-height: 1.15;
    width: 180px;
  }
  .brand__dot {
    flex: none; width: 34px; height: 34px; border-radius: 50%;
    background: var(--amber);
  }

  .person { position: absolute; left: 28px; top: 112px; padding-left: 12px; }
  .person::before {
    content: ""; position: absolute; left: 0; top: 5px;
    width: 5px; height: 26px; background: var(--amber);
  }
  .person__name { font-size: 26px; font-weight: 700; line-height: 1.2; white-space: nowrap; }
  .person__first { color: var(--amber); }
  .person__last { color: var(--navy); }
  .person__role { font-size: 14px; color: var(--ink); margin-top: 2px; }

  .details {
    position: absolute; left: 28px; top: 186px;
    font-size: 13px; color: var(--ink); line-height: 1.45;
  }
  .details__address { margin-bottom: 10px; }
  .details__line { display: flex; align-items: center; gap: 7px; white-space: nowrap; }
  .details__line svg { flex: none; }

  .partners {
    position: absolute; left: 330px; top: 30px;
    display: flex; flex-direction: column; align-items: center; gap: 14px;
  }
  .partner {
    display: flex; align-items: center; gap: 6px;
    font-size: 15px; font-weight: 400; color: var(--ink);
    letter-spacing: .5px;
  }
  .partner__mark {
    width: 14px; height: 14px; border-radius: 50%; background: var(--navy);
  }
  .partner-badge {
    width: 56px; height: 56px; border-radius: 50%;
    background: #3a6fc2; opacity: .85;
  }

  .back-brand {
    position: absolute; left: 0; right: 0; top: 70px;
    display: flex; flex-direction: column; align-items: center; gap: 14px;
  }
  .back-brand__disc {
    width: 84px; height: 84px; border-radius: 50%; background: var(--gold-deep);
  }
  .back-brand__name {
    color: var(--gold-deep); font-weight: 700; font-size: 24px; white-space: nowrap;
  }
  .distributor {
    position: absolute; left: 0; right: 0; bottom: 28px;
    display: flex; flex-direction: column; align-items: center; gap: 4px;
  }
  .distributor__label {
    font-size: 12px; font-weight: 600; color: var(--navy);
    letter-spacing: 1.5px; text-transform: uppercase;
  }
  .distributor__brand {
    display: flex; align-items: center; gap: 7px;
    font-size: 18px; font-weight: 700; color: var(--navy); letter-spacing: 1px;
  }
  .distributor__mark {
    width: 14px; height: 14px; border-radius: 50%; background: var(--navy);
  }
</style>
</head>
<body>
<div class="canvas">

  <section class="card card--front" aria-label="Business card front">
    <svg class="card__art" viewBox="0 0 560 320" width="560" height="320">
      <defs>
        <linearGradient id="leafGrad" x1="0" y1="0" x2="1" y2="1">
          <stop offset="0" stop-color="#8fbf5d"/>
          <stop offset=".55" stop-color="#4f8a3a"/>
          <stop offset="1" stop-color="#2f5e25"/>
        </linearGradient>
      </defs>
      <path d="M210 320 C235 225, 360 140, 560 112 L560 126 C370 150, 262 232, 236 320 Z" fill="#f5a412"/>
      <path d="M262 250 C320 170, 420 120, 560 100 L560 126 C420 140, 330 190, 270 260 Z" fill="#26357a"/>
      <path d="M236 320 C262 232, 370 150, 560 126 L560 320 Z"
            fill="url(#leafGrad)" role="img"
            aria-label="Photo of a rider in a wide-brimmed hat on a palomino horse among green willow trees"/>
    </svg>

    <div class="brand">
      <span class="brand__dot"></span>
      <span>Harrowfield Horse Supplies</span>
    </div>

    <div class="person">
      <p class="person__name"><span class="person__first">Marta</span> <span class="person__last">Velinska</span></p>
      <p class="person__role">Owner</p>
    </div>

    <div class="details">
      <p class="details__address">27 Lindqvist Rd<br>Marrowbank Q 4587</p>
      <p class="details__line">
        <svg width="11" height="11" viewBox="0 0 12 12"><path d="M3 1 L5 3.5 L3.8 5 C4.5 6.5 5.5 7.5 7 8.2 L8.5 7 L11 9 L9.5 11 C5 10.5 1.5 7 1 2.5 Z" fill="#f5a412"/></svg>
        1300 48 62 90
      </p>
      <p class="details__line">
        <svg width="11" height="11" viewBox="0 0 12 12"><circle cx="6" cy="6" r="5.2" fill="none" stroke="#f5a412" stroke-width="1.4"/><path d="M1 6 H11 M6 1 C3.5 3.5 3.5 8.5 6 11 M6 1 C8.5 3.5 8.5 8.5 6 11" fill="none" stroke="#f5a412" stroke-width="1"/></svg>
        www.harrowfields.net.au
      </p>
    </div>

    <div class="partners">
      <div class="partner"><span class="partner__mark"></span><span>TRAILGEM</span></div>
      <div class="partner-badge" role="img" aria-label="Partner badge"></div>
    </div>
  </section>

  <section class="card card--back" aria-label="Business card back">
    <div class="back-brand">
      <span class="back-brand__disc"></span>
      <span class="back-brand__name">Harrowfield Horse Supplies</span>
    </div>
    <div class="distributor">
      <span class="distributor__label">Distributors of</span>
      <span class="distributor__brand"><span class="distributor__mark"></span>TRAILGEM</span>
    </div>
  </section>

</div>
</body>
</html>
```